TREVAL BUILDWORKS, LLC Webpage portfolio

I want to create a Website that allows my potential clients to browse my Skilled work via before and after photos. I want the website to enhance the work that I provide and potentially drive new business, or at least solidify my work.
I also do 3D CAD and Modeling of New Spaces and it would be nice to show some of that work from pencil design to 3D modeling, which I feel may help give me more clients.

The website needs to show a solid carpenter/company with the skills to get any project completed.

Types of Jobs - Custom Carpentry & Finishes, Kitchens, Baths, Basements, Decks, Porches, Whole House Renovation - Skilled Craftsmanship (Hardwood Flooring, Floor and Wall Tile) and much more...

Target Market(s)

Residential Home Renovation, Kitchen and Bath Renovation, Home Improvement

Industry/Entity Type

Residential Construction

Number of Pages Required

5+ page

Font styles to use
Sans Serif
Script

Requirements
Must have
• Similar to Plinvo.com, except for Treval Buildworks.
• Must be inviting.
• My Services Offered
• A way to reach me or contact me for estimates with some sort of Screening Questionare.
Nice to have
• Inviting Colors
Should not have
• Not sure at this time

```html
<!DOCTYPE html>
<html lang="en">
<head>
<meta charset="utf-8">
<title>Treval Buildworks — Portfolio</title>
<link rel="stylesheet" href="https://fonts.googleapis.com/css2?family=Questrial&display=swap">
<style>
:root{
  --bg:#1a1a1a;
  --bg-deep:#121212;
  --panel:#252525;
  --text:#d8d8d8;
  --text-dim:#9a9a9a;
  --white:#f2f2f2;
}
*{margin:0;padding:0;box-sizing:border-box}
html,body{width:778px;height:1200px;overflow:hidden}
body{
  position:relative;
  font-family:"Questrial",sans-serif;
  color:var(--text);
  background:radial-gradient(ellipse at 50% 40%,#1f1f1f 0%,var(--bg) 55%,var(--bg-deep) 100%);
}
.abs{position:absolute}
.brand{left:34px;top:16px;display:flex;align-items:center;gap:6px;font-size:12px;color:var(--white);letter-spacing:.3px}
.brand-mark{width:10px;height:10px;background:var(--white)}
.social{display:flex;gap:9px}
.social span{width:7px;height:7px;border-radius:50%;background:var(--white);display:block}
.social-top{left:496px;top:19px}
.phone{right:32px;top:10px;font-size:17.5px;color:var(--white);letter-spacing:.3px}
.nav{right:32px;top:63px;display:flex;gap:13px;font-size:9px;color:var(--text-dim);letter-spacing:.2px}
.heading{left:32px;font-size:21.5px;line-height:28px;color:var(--white);font-weight:400;letter-spacing:.6px}
.small{font-size:7px;line-height:9.3px;color:var(--text-dim);text-transform:uppercase}
.services{left:32px;top:193px;width:115px}
.services p{margin-bottom:10px}
.services .big{font-size:11px;line-height:14.5px;margin:28px 0 38px}
.panel{left:194px;width:552px;height:260px;background:var(--panel);box-shadow:0 0 14px rgba(0,0,0,.6)}
.photo{left:227px;width:487px;height:195px}
.cad{top:227px;background:linear-gradient(90deg,#6d6d6d 0%,#5a5a5a 28%,#505050 60%,#5c5c5c 100%)}
.counter{top:616px;background:linear-gradient(160deg,#7a4a2c 0%,#b08a6a 30%,#6b3d20 60%,#8a4f2a 100%)}
.thumb{left:32px;top:649px;width:162px;height:162px;background:linear-gradient(135deg,#4a3020 0%,#6b4a35 45%,#2a2622 100%)}
.arrows{left:32px;top:591px}
.social-mid{left:32px;top:835px}
.social-foot{left:32px;top:1159px}
.intro{left:32px;top:1005px;width:115px}
.testimonial{top:1005px;width:90px;font-size:7px;line-height:9.3px;color:var(--text-dim)}
.testimonial .quote{height:64px}
.testimonial .name{color:var(--white);text-transform:uppercase}
.testimonial .role{color:var(--white)}
.testimonial .stars{margin-top:18px;color:var(--white);font-size:8px;letter-spacing:2px}
</style>
</head>
<body>
<header>
  <div class="abs brand"><span class="brand-mark"></span>Treval Buildworks</div>
  <div class="abs social social-top" aria-label="Social links"><span></span><span></span><span></span><span></span></div>
  <div class="abs phone">+1 (555) 014-2273</div>
  <nav class="abs nav"><span>KITCHENS</span><span>BATHS</span><span>BASEMENTS</span><span>FINISHED CARPENTRY</span><span>DECKS &amp; PORCHES</span></nav>
</header>

<section>
  <h2 class="abs heading" style="top:94px">MY<br>SERVICES</h2>
  <div class="abs services small">
    <p>3D CAD modelling of new spaces</p>
    <p>Custom<br>carpentry &amp; finishes,</p>
    <p>Kitchens,<br>baths,<br>basements,<br>decks,<br>porches,</p>
    <p class="big">Whole house<br>renovation</p>
    <p>Skilled craftsmanship (hardwood flooring, floor and wall tile)</p>
    <p>And much more</p>
  </div>
  <div class="abs panel" style="top:194px"></div>
  <div class="abs photo cad" role="img" aria-label="Interior rendering transitioning from CAD line drawing to finished 3D living room"></div>
</section>

<section>
  <h2 class="abs heading" style="top:516px">BROWSE<br>MY WORK</h2>
  <svg class="abs arrows" width="60" height="18" viewBox="0 0 60 18" aria-label="Previous and next">
    <polyline points="8,2 2,9 8,16" fill="none" stroke="#f2f2f2" stroke-width="1.5"/>
    <polyline points="44,2 50,9 44,16" fill="none" stroke="#f2f2f2" stroke-width="1.5"/>
  </svg>
  <div class="abs thumb" role="img" aria-label="Stone column and hardwood floor detail"></div>
  <div class="abs panel" style="top:584px"></div>
  <div class="abs photo counter" role="img" aria-label="Curved granite kitchen countertop with wood cabinets"></div>
  <div class="abs social social-mid" aria-label="Social links"><span></span><span></span><span></span><span></span></div>
</section>

<section>
  <h2 class="abs heading" style="top:905px">CLIENT<br>TESTIMONIALS</h2>
  <p class="abs intro small">Read what our satisfied clients have to say about our services and expertise.</p>
  <div class="abs testimonial" style="left:194px"><p class="quote">Lorem ipsum dolor sit amet, consectetur adipiscing elit. ..</p><p class="name">John Doe</p><p class="role">Entrepreneur</p><p class="stars">★★★★★</p></div>
  <div class="abs testimonial" style="left:305px"><p class="quote">Lorem ipsum dolor sit amet, consectetur adipiscing elit. ..</p><p class="name">John Doe</p><p class="role">Entrepreneur</p><p class="stars">★★★★★</p></div>
  <div class="abs testimonial" style="left:415px"><p class="quote">Lorem ipsum dolor sit amet, consectetur adipiscing elit. ..</p><p class="name">John Doe</p><p class="role">Entrepreneur</p><p class="stars">★★★★★</p></div>
  <div class="abs testimonial" style="left:525px"><p class="quote">Lorem ipsum dolor sit amet, consectetur adipiscing elit. ..</p><p class="name">John Doe</p><p class="role">Entrepreneur</p><p class="stars">★★★★★</p></div>
  <div class="abs social social-foot" aria-label="Social links"><span></span><span></span><span></span><span></span></div>
</section>
</body>
</html>
```